Valdane Companies Business Card Design

We need a new business card for our Private Equity Real Estate Development firm, “Valdane” and our EB-5 regional center “Thornmere Regional Center” on one card. We prefer a design that is simple, elegant, and represents the luxury products we design and build as well as the financial security and stability our successful history has produced. We are an industry leader in our field and 3rd generation family business that has evolved into an institutional quality investment platform. Considered design size is standard business card dimensions (3.5 x 2 inches with an additional 1/8 inch space for design elements or backgrounds that extend beyond the finished size of your piece.

Target Market(s)

• High net worth individuals
• Highly skilled technical workers and physicians in the US seeking investment-based immigration opportunities
• Sophisticated private equity investors
• Intermediary partners include domestic attorneys and investment brokers, as well as international agent networks
• US real estate developers

Industry/Entity Type

Finance

Contact Information for Business Card

(Providing placeholder info for personal information, please design for longer character spaces, longer names and addresses etc..)
• Logo for Valdane
• Logo for Thornmere Regional Center
• Full name: Marcus Valdane
• Job title: CEO
• Email address: mvaldane@valdanecompanies.com
• Cell phone number: +1.555.314.2287
• Office number +1.555.628.4410
• Office address: Larkfield Court 5, 4817 Vista Orilla, San Ramon, CA.
• Website: www.valdanecompanies.com

Font styles to use
Serif
Sans Serif

Colors
ec1f27
ffffff
000000

Requirements
Must have
• • Logo for Valdane
• • Logo for Thornmere Regional Center
• - Use rounded corners
• (See .ai file included for logos)
Nice to have
• • Simple, elegant design
• • Aesthetically compatible with our website design (www.valdanecompanies.com)
• • Color palette including but not limited to white, black, and red (as per logos)
Should not have
• - Not too much red color
• - Do not stack both logos on top of each other

```html
<!DOCTYPE html>
<html lang="en">
<head>
<meta charset="utf-8">
<title>Valdane Companies – Business Card</title>
<link rel="stylesheet" href="https://fonts.googleapis.com/css2?family=Roboto:wght@400;500;700&display=swap">
<style>
  :root {
    --page: #2b2b2b;
    --card-dark: #1f1f1f;
    --card-light: #ffffff;
    --ink: #111111;
    --ink-soft: #2a2a2a;
    --silver: #d9d9d9;
    --rule-dark: #8a8a8a;
    --rule-light: #444444;
  }
  * { box-sizing: border-box; margin: 0; padding: 0; }
  html, body { width: 1200px; height: 1200px; overflow: hidden; }
  body {
    background: var(--page);
    font-family: "Roboto", Arial, sans-serif;
    position: relative;
  }
  .card {
    position: absolute;
    left: 180px;
    width: 840px;
    height: 480px;
    border-radius: 22px;
    box-shadow: 0 10px 30px rgba(0,0,0,.35);
  }
  .card--front { top: 90px; background: var(--card-dark); }
  .card--back  { top: 630px; background: var(--card-light); }

  .brand {
    position: absolute;
    display: flex;
    align-items: center;
  }
  .brand__mark {
    width: 56px; height: 56px;
    border: 4px solid currentColor;
  }
  .brand__rule {
    width: 2px; height: 86px;
    margin: 0 28px;
  }
  .brand__name {
    font-weight: 500;
    text-transform: uppercase;
    letter-spacing: .08em;
    line-height: 1;
  }

  .card--front .brand { left: 120px; top: 197px; color: var(--silver); }
  .card--front .brand__rule { background: var(--rule-dark); }
  .card--front .brand__name { font-size: 38px; }

  .card--back .brand { left: 60px; top: 52px; color: var(--ink); }
  .card--back .brand__mark { width: 50px; height: 50px; }
  .card--back .brand__rule { background: var(--rule-light); height: 76px; margin: 0 24px; }
  .card--back .brand__name { font-size: 40px; }

  .person {
    position: absolute;
    left: 64px; top: 200px;
    color: var(--ink-soft);
  }
  .person__name { font-size: 28px; font-weight: 700; color: var(--ink); }
  .person__title, .person__address { font-size: 19px; line-height: 1.25; margin-top: 4px; }

  .contact {
    position: absolute;
    left: 64px; top: 330px;
    list-style: none;
    font-size: 19px;
    color: var(--ink-soft);
  }
  .contact li { display: flex; align-items: center; height: 28px; }
  .contact svg { width: 18px; height: 18px; margin-right: 36px; fill: none; stroke: var(--ink); stroke-width: 1.8; }
</style>
</head>
<body>

<section class="card card--front" aria-label="Card front">
  <div class="brand">
    <span class="brand__mark"></span>
    <span class="brand__rule"></span>
    <span class="brand__name">Thornmere Regional Center</span>
  </div>
</section>

<section class="card card--back" aria-label="Card back">
  <div class="brand">
    <span class="brand__mark"></span>
    <span class="brand__rule"></span>
    <span class="brand__name">Valdane Capital</span>
  </div>

  <div class="person">
    <p class="person__name">Marcus Valdane</p>
    <p class="person__title">CEO</p>
    <p class="person__address">Larkfield Court 5, 4817<br>Vista Orilla San Ramon, CA</p>
  </div>

  <ul class="contact">
    <li><svg viewBox="0 0 18 18"><rect x="4.5" y="1" width="9" height="16" rx="1.5"/><line x1="8" y1="14.5" x2="10" y2="14.5"/></svg>+1555 - 314 - 2287</li>
    <li><svg viewBox="0 0 18 18"><path d="M2 6c0-2 3-3 7-3s7 1 7 3v1h-3.5V5.5h-7V7H2z"/><rect x="3" y="8" width="12" height="8" rx="1"/></svg>+1555 - 628 - 4410</li>
    <li><svg viewBox="0 0 18 18"><rect x="1.5" y="4" width="15" height="10"/><polyline points="1.5,4 9,10 16.5,4"/></svg>mvaldane@valdanecompanies.com</li>
    <li><svg viewBox="0 0 18 18"><circle cx="9" cy="9" r="7.5"/><ellipse cx="9" cy="9" rx="3.2" ry="7.5"/><line x1="1.5" y1="9" x2="16.5" y2="9"/></svg>www.valdanecompanies.com</li>
  </ul>
</section>

</body>
</html>
```